Business cards to launch an education platform

Hi,
I am looking at having new business cards designed.
I am a startup, developing a web platform for schools and university, the education world. It's an online assessment system.
I would like a card that looks classy, and that is using the colors and the font of my logo.

I have attached:
1) my logo
2) A business card that I have designed quickly so you can have all the information required in the card, but I really don't like it.
3) The font that I am using (Lato Regular) to design my web platform
4) Some screenshots of my web platform so you can have a look at the style that I have.

Target Market(s)

Major market: Education system: Schools and university
Minor markets: Business in general

Industry/Entity Type

Business

Contact Information for Business Card

Clara Fenwick
Director

M: 0437 518 902
E: clara.fenwick@amberLoomSystems.com.au

Requirements
Must have
• The colors of my logo

```html
<!DOCTYPE html>
<html lang="en">
<head>
<meta charset="utf-8">
<title>Amber Loom systems – Business Card</title>
<link href="https://fonts.googleapis.com/css2?family=Lato:wght@400;700&display=swap" rel="stylesheet">
<style>
  :root {
    --page-bg: #e9e7e3;
    --card-white: #ffffff;
    --navy: #0b3f74;
    --sky: #1a8ed0;
    --brand-blue: #15497f;
    --text-light: #ffffff;
  }
  html, body {
    margin: 0;
    padding: 0;
    width: 1200px;
    height: 902px;
    overflow: hidden;
    background: var(--page-bg);
    font-family: "Lato", Arial, sans-serif;
  }
  .card {
    position: absolute;
    left: 150px;
    top: 194px;
    width: 900px;
    height: 514px;
    background: var(--card-white);
    overflow: hidden;
    box-shadow: 0 10px 30px rgba(0,0,0,0.18);
  }
  .card-wave {
    position: absolute;
    inset: 0;
    width: 900px;
    height: 514px;
  }
  .brand {
    position: absolute;
    left: 120px;
    top: 120px;
    display: flex;
    align-items: center;
    gap: 26px;
  }
  .brand-mark {
    width: 78px;
    height: 78px;
    background: var(--brand-blue);
  }
  .brand-name {
    font-size: 46px;
    font-weight: 400;
    letter-spacing: 3px;
    color: var(--brand-blue);
    white-space: nowrap;
  }
  .holder {
    position: absolute;
    left: 44px;
    top: 402px;
    color: var(--text-light);
  }
  .holder-name {
    font-size: 42px;
    font-weight: 700;
    line-height: 1;
    white-space: nowrap;
  }
  .holder-role {
    font-size: 28px;
    font-weight: 400;
    margin-top: 8px;
  }
  .divider {
    position: absolute;
    left: 340px;
    top: 395px;
    width: 2px;
    height: 92px;
    background: var(--text-light);
  }
  .contacts {
    position: absolute;
    left: 362px;
    top: 404px;
    color: var(--text-light);
    font-size: 24px;
    line-height: 1;
  }
  .contact-line {
    display: flex;
    align-items: center;
    gap: 12px;
    margin-bottom: 20px;
    white-space: nowrap;
  }
  .contact-icon {
    width: 24px;
    height: 24px;
    flex: none;
  }
</style>
</head>
<body>
  <div class="card">
    <svg class="card-wave" viewBox="0 0 900 514" aria-hidden="true">
      <path d="M0,318 C230,400 480,340 900,52 L900,514 L0,514 Z" fill="var(--sky)"/>
      <path d="M0,342 C250,420 500,360 900,84 L900,514 L0,514 Z" fill="var(--navy)"/>
    </svg>

    <div class="brand">
      <div class="brand-mark"></div>
      <div class="brand-name">Amber Loom systems</div>
    </div>

    <div class="holder">
      <div class="holder-name">Clara Fenwick</div>
      <div class="holder-role">Director</div>
    </div>

    <div class="divider"></div>

    <div class="contacts">
      <div class="contact-line">
        <svg class="contact-icon" viewBox="0 0 24 24" aria-hidden="true">
          <rect x="1" y="1" width="22" height="22" fill="none" stroke="#fff" stroke-width="2"/>
          <path d="M6 9 C6 7 8 6 12 6 C16 6 18 7 18 9 L15 10 L14 8.5 L10 8.5 L9 10 Z" fill="#fff"/>
          <rect x="7" y="11" width="10" height="7" fill="#fff"/>
        </svg>
        <span>0437 518 902</span>
      </div>
      <div class="contact-line">
        <svg class="contact-icon" viewBox="0 0 24 24" aria-hidden="true">
          <rect x="1" y="4" width="22" height="16" fill="none" stroke="#fff" stroke-width="2"/>
          <path d="M2 5 L12 13 L22 5" fill="none" stroke="#fff" stroke-width="2"/>
        </svg>
        <span>clara.fenwick@amberLoomSystems.com.au</span>
      </div>
    </div>
  </div>
</body>
</html>
```